Wed site for biomedical device startup

We need a generic website for a medical device startup. I will provide examples below of websites from other companies that can serve as models for what we are looking for. The startup is for a device that can non invasively measure blood flow in the brain using light. The application is to detect the type of stroke someone is having before they get to the hospital so treatment can be started right away. This saves patients upto hours of delayed treatment. Patients will be able to recover from stroke much better and faster as a result. I have attached an AI generated illustration of what the device will ultimately look like for reference.

https://www.372clinicaltech.com
https://vextalune.com

Target Market(s)

Biomedical, medical device, investors of biomedical device startups

Industry/Entity Type

Biomedical

Coding

Coded - Design and coding required

Number of Pages Required

4 page

Requirements
Must have
• same section and section headings as example websites listed above
Nice to have
• similar to example websites listed above. Prefer a darker website over a lighter one. Perhaps dark blues to go with logo colors. A moving background image element at top of landing page could be cool. Something indicative of heartbeat, or neurons, or blood flow.

```html
<!DOCTYPE html>
<html lang="en">
<head>
<meta charset="utf-8">
<title>NUVIRA — Biomedical Insight</title>
<link rel="stylesheet" href="https://fonts.googleapis.com/css2?family=Open+Sans:wght@400;600;700&family=Ubuntu:wght@400;500;700&display=swap">
<style>
:root{
  --navy:#05043a;
  --navy-deep:#03022a;
  --navy-soft:#0d1250;
  --cyan:#2aa7e0;
  --white:#ffffff;
  --muted:#d9dbef;
  --violet:#7a2ee0;
  --magenta:#e0308f;
}
*{margin:0;padding:0;box-sizing:border-box}
html,body{width:1200px;height:4415px;overflow:hidden;background:var(--navy);color:var(--white);font-family:"Open Sans",sans-serif}
.page{position:relative;width:1200px;height:4415px}
.abs{position:absolute}
h1,h2,h3{font-family:"Ubuntu",sans-serif;font-weight:400}
p{font-size:14px;line-height:32px;color:var(--white)}

/* nav */
.nav{top:0;left:0;width:1200px;height:76px;background:var(--navy);z-index:5}
.brand{display:flex;align-items:center;gap:10px;left:110px;top:8px}
.brand-dot{width:52px;height:52px;border-radius:50%;background:linear-gradient(135deg,var(--cyan),var(--violet))}
.brand-name{font-family:"Ubuntu",sans-serif;font-size:38px;letter-spacing:2px}
.menu{display:flex;right:100px;top:24px;list-style:none;font-size:17px}
.menu li{padding:4px 21px;border-radius:16px}
.menu .active{background:var(--cyan);font-weight:700}

/* pill button */
.btn{display:flex;align-items:center;gap:14px;background:var(--white);color:#111;border-radius:24px;height:42px;padding:0 3px 0 22px;font-size:14px}
.btn .dot{width:36px;height:36px;border-radius:50%;background:linear-gradient(135deg,var(--cyan),var(--violet) 60%,var(--magenta))}

/* hero */
.hero{top:76px;left:0;width:1200px;height:670px;background:
  radial-gradient(ellipse 260px 220px at 50% 62%,rgba(90,200,255,.85),transparent 70%),
  radial-gradient(ellipse 200px 240px at 22% 58%,rgba(230,60,190,.7),transparent 70%),
  radial-gradient(ellipse 200px 240px at 72% 55%,rgba(240,50,150,.7),transparent 70%),
  radial-gradient(ellipse 240px 200px at 90% 60%,rgba(60,120,255,.6),transparent 70%),
  radial-gradient(ellipse 240px 200px at 6% 62%,rgba(60,120,255,.55),transparent 70%),
  linear-gradient(180deg,#03021e 0%,#070540 35%,#1b1aa0 70%,#2a1f9a 100%)}
.hero-title{top:80px;width:1200px;text-align:center;font-size:58px;font-weight:700;font-family:"Open Sans",sans-serif}
.hero-sub{top:162px;width:1200px;text-align:center;font-size:19px}
.hero .btn{top:218px;left:512px;position:absolute;height:50px;padding-left:26px;font-size:16px}
.hero .btn .dot{width:44px;height:44px}

.wave{left:0;width:1200px}

.sec-head{font-size:44px;line-height:60px}
.about-img{left:126px;top:791px;width:424px;height:424px;border-radius:50%;background:
  radial-gradient(circle at 30% 18%,#f3f3f3 0 18%,transparent 30%),
  radial-gradient(circle at 85% 15%,#c9cdd3 0 14%,transparent 28%),
  radial-gradient(circle at 78% 62%,#1a1c22 0 14%,transparent 24%),
  radial-gradient(ellipse at 40% 60%,#e7b79b,#c98d70 60%,#9a6a55)}

.help{top:1277px;left:0;width:1200px;height:437px;background:radial-gradient(ellipse at 80% 20%,#1a3a7a,var(--navy-soft) 45%,var(--navy-deep))}
.center{width:1200px;text-align:center}

.photo{background:
  radial-gradient(ellipse 160px 260px at 20% 30%,#3f6b2a,transparent 70%),
  radial-gradient(ellipse 170px 120px at 62% 42%,#e9e9e6,transparent 70%),
  radial-gradient(ellipse 140px 120px at 55% 62%,#b88466,transparent 70%),
  radial-gradient(ellipse 260px 120px at 45% 92%,#dadbd8,transparent 70%),
  radial-gradient(ellipse 120px 160px at 88% 60%,#1d2229,transparent 70%),
  linear-gradient(135deg,#7e8a86,#c4c6c0 55%,#5a5e60)}
.photo-face{background:
  radial-gradient(ellipse 230px 280px at 78% 55%,#b98467,#7a5040 45%,transparent 75%),
  radial-gradient(ellipse 150px 220px at 40% 40%,#3b2a22,transparent 70%),
  linear-gradient(110deg,#0a0808,#1d1511 50%,#2d211b)}

.focus{top:2760px;left:0;width:1200px;height:394px;background:radial-gradient(ellipse at 50% 0%,#0d1a5c,var(--navy-deep) 70%)}
.accordion{left:166px;top:3007px;width:866px;height:54px;border-top:2px solid var(--muted);border-bottom:2px solid var(--muted);display:flex;align-items:center;justify-content:space-between;padding:0 6px;font-size:24px;font-family:"Ubuntu",sans-serif;letter-spacing:.5px}

.team{top:3154px;left:0;width:1200px;height:514px;background:var(--navy)}
.member{width:222px;text-align:center;top:3305px}
.member .avatar{width:222px;height:222px;border-radius:50%}
.av1{background:radial-gradient(ellipse 90px 70px at 50% 85%,#f6f6f4,transparent 70%),radial-gradient(circle at 50% 40%,#6e4a3a 0 22%,transparent 32%),linear-gradient(160deg,#a9d6d8,#7fc1c6)}
.av2{background:radial-gradient(ellipse 100px 70px at 50% 88%,#8fb2d6,transparent 70%),radial-gradient(circle at 50% 38%,#c4957a 0 20%,transparent 30%),linear-gradient(160deg,#f2f2f0,#dcdcda)}
.av3{background:radial-gradient(ellipse 100px 70px at 50% 88%,#d8c6a8,transparent 70%),radial-gradient(circle at 50% 36%,#e2e0dc 0 24%,transparent 34%),linear-gradient(160deg,#e8e3dc,#c9c2b8)}
.av4{background:radial-gradient(ellipse 100px 70px at 50% 88%,#3f4c63,transparent 70%),radial-gradient(circle at 50% 38%,#b88a70 0 20%,transparent 30%),linear-gradient(160deg,#dfe6ee,#9fb0c0)}
.member .name{margin-top:26px;font-size:17px}
.member .role{margin-top:6px;font-size:17px;color:var(--cyan)}

.question{top:3668px;left:0;width:1200px;height:440px;background:radial-gradient(ellipse at 50% 30%,#14206a,var(--navy-deep) 70%)}

.footer{top:4097px;left:0;width:1200px;height:318px;background:var(--navy)}
.foot-head{font-family:"Ubuntu",sans-serif;font-size:26px}
.foot-links{list-style:none;font-size:16px;line-height:38.5px}
.contact-row{display:flex;align-items:center;gap:16px;font-size:16px;height:50px}
.social{display:flex;gap:6px;left:512px;top:4281px}
.social span{width:32px;height:32px;border-radius:50%;background:var(--cyan);border:3px solid var(--white);box-shadow:0 0 0 1px var(--cyan)}
.rule{left:110px;top:4376px;width:980px;height:1px;background:var(--muted)}
</style>
</head>
<body>
<div class="page">

  <header class="nav abs">
    <div class="brand abs"><span class="brand-dot"></span><span class="brand-name">NUVIRA</span></div>
    <ul class="menu abs">
      <li class="active">Home</li><li>About</li><li>Technology</li><li>Publications</li><li>Contact</li>
    </ul>
  </header>

  <section class="hero abs" role="img" aria-label="Neon heartbeat waveform over a glowing blue and pink grid">
    <h1 class="hero-title abs">Revolutionizing Biomedical Insight</h1>
    <p class="hero-sub abs">Precision solutions that transform patient outcomes through advanced technology and data.</p>
    <div class="btn"><span>Learn More</span><span class="dot"></span></div>
  </section>
  <svg class="wave abs" style="top:596px" width="1200" height="160" viewBox="0 0 1200 160">
    <path d="M0 70 C80 30 130 10 200 60 S330 160 420 140 S560 20 620 15 S760 110 850 130 S1050 60 1200 70 L1200 160 L0 160Z" fill="var(--navy)"/>
    <path d="M0 70 C80 30 130 10 200 60 S330 160 420 140 S560 20 620 15 S760 110 850 130 S1050 60 1200 70" fill="none" stroke="#fff" stroke-width="4"/>
  </svg>

  <section>
    <div class="about-img abs" role="img" aria-label="Patient wearing forehead light sensors beside a handheld monitor"></div>
    <h2 class="sec-head abs" style="left:643px;top:776px">Pioneering the<br>Future of Biomedical<br>Technology</h2>
    <p class="abs" style="left:643px;top:968px;width:430px">We are a biomedical innovation company focused on developing cutting-edge solutions for diagnostics, monitoring, and patient care. Leveraging data science, machine learning, and deep clinical insight, our mission is to empower clinicians and improve lives.</p>
    <div class="btn abs" style="left:646px;top:1148px"><span>Learn More</span><span class="dot"></span></div>
  </section>

  <section class="help abs">
    <h2 class="center abs" style="top:70px;font-size:46px">How We Help</h2>
    <p class="center abs" style="top:126px;color:var(--cyan);font-size:16px">Solving the Critical Gaps in Patient Monitoring &amp; Decision-Making</p>
    <p class="abs" style="left:250px;top:176px;width:700px;text-align:center;line-height:35px;font-size:15px">We're redefining what's possible in biomedical monitoring. Our technology captures and interprets real-time physiological data, empowering clinicians with the clarity they need to act fast, treat earlier, and improve patient outcomes. Whether in high-acuity environments or chronic care, we deliver insight when timing is critical.</p>
    <div class="btn abs" style="left:523px;top:332px"><span>Learn More</span><span class="dot"></span></div>
  </section>

  <section>
    <div class="photo abs" style="left:0;top:1714px;width:597px;height:515px" role="img" aria-label="Man resting in a clinic chair wearing a sensor headset and headphones"></div>
    <h2 class="sec-head abs" style="left:643px;top:1790px">Life-changing<br>Technology For<br>mature Infants</h2>
    <p class="abs" style="left:643px;top:1978px;width:430px">Lorem ipsum dolor sit amet, consectetur adipiscing elit, sed do eiusmod tempor incididunt ut labore et dolore magna aliqua. Ut enim ad minim veniam, quis nostrud exercitation ullamco laboris nisi ut aliquip ex ea commodo consequat.</p>
    <div class="btn abs" style="left:643px;top:2156px"><span>Learn More</span><span class="dot"></span></div>
  </section>

  <section>
    <h2 class="sec-head abs" style="left:113px;top:2312px">NIRDS explained</h2>
    <p class="abs" style="left:113px;top:2398px;width:430px">Lorem ipsum dolor sit amet, consectetur adipiscing elit, sed do eiusmod tempor incididunt ut labore et dolore magna aliqua. Ut enim ad minim veniam, quis nostrud exercitation ullamco laboris nisi ut aliquip ex ea commodo consequat.</p>
    <div class="btn abs" style="left:111px;top:2586px"><span>Learn More</span><span class="dot"></span></div>
    <div class="photo-face abs" style="left:600px;top:2229px;width:600px;height:531px" role="img" aria-label="Close portrait of a woman in low light, turned to the side"></div>
  </section>

  <section class="focus abs">
    <h2 class="center abs" style="top:78px;font-size:44px;line-height:58px">Now The Focus Shifts To Decreasing Disabilities<br>And Improving Long-term Outcomes.</h2>
  </section>
  <div class="accordion abs"><span>PUBLICATIONS</span>
    <svg width="26" height="16" viewBox="0 0 26 16"><path d="M2 2 L13 13 L24 2" fill="none" stroke="#fff" stroke-width="2.5"/></svg>
  </div>

  <section class="team abs">
    <h2 class="abs" style="left:113px;top:58px;font-size:44px;font-weight:700">Our Team</h2>
  </section>
  <svg class="abs" style="left:1035px;top:3221px" width="52" height="22" viewBox="0 0 52 22">
    <circle cx="10" cy="11" r="10" fill="#fff"/><path d="M14 11 H6 M9 7 L5 11 L9 15" stroke="var(--navy)" stroke-width="2" fill="none"/>
    <circle cx="40" cy="11" r="10" fill="#6c6e94"/><path d="M36 11 H44 M41 7 L45 11 L41 15" stroke="var(--navy)" stroke-width="2" fill="none"/>
  </svg>
  <div class="member abs" style="left:113px"><div class="avatar av1" role="img" aria-label="Portrait of team member Mara Ellison"></div><div class="name">Mara Ellison</div><div class="role">CEO</div></div>
  <div class="member abs" style="left:364px"><div class="avatar av2" role="img" aria-label="Portrait of team member Dev Ralston"></div><div class="name">Dev Ralston</div><div class="role">CEO</div></div>
  <div class="member abs" style="left:612px"><div class="avatar av3" role="img" aria-label="Portrait of team member Helen Marsh"></div><div class="name">Helen Marsh</div><div class="role">Founder</div></div>
  <div class="member abs" style="left:863px"><div class="avatar av4" role="img" aria-label="Portrait of team member Omar Castell"></div><div class="name">Omar Castell</div><div class="role">Controller</div></div>

  <section class="question abs">
    <h2 class="center abs" style="top:70px;font-size:44px;font-weight:700">Have a Question? We're Here to Help</h2>
    <p class="abs" style="left:160px;top:150px;width:880px;text-align:center;line-height:29px">Sed ut perspiciatis unde omnis iste natus error sit voluptatem accusantium doloremque laudantium, totam rem aperiam, eaque ipsa quae ab illo inventore veritatis et quasi architecto beatae vitae dicta sunt explicabo. Nemo enim ipsam voluptatem quia voluptas sit aspernatur aut odit aut fugit.</p>
    <div class="btn abs" style="left:523px;top:244px"><span>Contact Us</span><span class="dot"></span></div>
  </section>
  <svg class="wave abs" style="top:3940px" width="1200" height="160" viewBox="0 0 1200 160">
    <path d="M0 80 C80 130 160 160 240 110 S380 20 460 20 S560 100 620 120 S740 130 820 80 S960 20 1040 60 S1150 150 1200 110 L1200 160 L0 160Z" fill="var(--navy)"/>
    <path d="M0 80 C80 130 160 160 240 110 S380 20 460 20 S560 100 620 120 S740 130 820 80 S960 20 1040 60 S1150 150 1200 110" fill="none" stroke="#fff" stroke-width="4"/>
  </svg>

  <footer class="footer abs">
    <h3 class="foot-head abs" style="left:113px;top:20px">Quick Links</h3>
    <ul class="foot-links abs" style="left:110px;top:66px">
      <li>Home</li><li>About</li><li>Technology</li><li>Publications</li><li>Contact</li>
    </ul>
    <div class="abs" style="left:404px;top:50px;display:flex;align-items:center;gap:18px">
      <span style="width:112px;height:112px;border-radius:50%;background:linear-gradient(135deg,var(--cyan),var(--violet))"></span>
      <span style="font-family:'Ubuntu',sans-serif;font-size:72px;letter-spacing:4px">NUVIRA</span>
    </div>
    <h3 class="foot-head abs" style="left:893px;top:18px">Help Links</h3>
    <div class="abs" style="left:893px;top:60px">
      <div class="contact-row">
        <svg width="24" height="28" viewBox="0 0 24 28"><path d="M12 2 C6 2 3 6 3 11 C3 18 12 26 12 26 C12 26 21 18 21 11 C21 6 18 2 12 2Z" fill="#fff"/><circle cx="12" cy="11" r="4" fill="var(--navy)"/></svg>
        <span>Harbor Row, USA -500210</span></div>
      <div class="contact-row">
        <svg width="24" height="24" viewBox="0 0 24 24"><circle cx="12" cy="12" r="12" fill="#fff"/><path d="M8 6 L10 9 L9 11 C10 13 11 14 13 15 L15 14 L18 16 L17 18 C12 18 6 12 6 7Z" fill="var(--navy)"/></svg>
        <span>+1 555 014 2290</span></div>
      <div class="contact-row">
        <svg width="26" height="24" viewBox="0 0 26 24"><circle cx="13" cy="12" r="12" fill="#fff"/><rect x="6" y="7" width="14" height="10" fill="var(--navy)"/><path d="M6 7 L13 13 L20 7" stroke="#fff" stroke-width="1.5" fill="none"/></svg>
        <span>hello@nuvira.com</span></div>
    </div>
  </footer>
  <div class="social abs" aria-label="Social profiles"><span></span><span></span><span></span><span></span><span></span></div>
  <div class="rule abs"></div>
  <p class="center abs" style="top:4386px;font-size:12px;line-height:22px">Copyright © 2025 NUVIRA | All Rights Reserved</p>

</div>
</body>
</html>
```